Verlindo Magician

I want the business card for my business to give to people who watch that later I will be employed to show magic here is my website http://www.balsamomagicien.com/I want the interesting design , i am very opened for formal and informal, I watch a lot of design so don't stick to the common shape and form but i hope it can also be produced the thing to write on will be the same as in picture that i will upload , i also will upload the logo for you that so can be easy to useDenis CostilleMagicianMAGICIAN BALSAMO 17 rue des Tilleuls - 48210 VALORCY contact@verlindoillusions.example tel. 0492 946 157 tel. 0674 219 503

```html
<!DOCTYPE html>
<html lang="en">
<head>
<meta charset="utf-8">
<title>Verlindo Magician – Business Card</title>
<link href="https://fonts.googleapis.com/css2?family=Open+Sans:wght@300;400;700&display=swap" rel="stylesheet">
<style>
  :root {
    --backdrop: #5f5f5f;
    --card-black: #000000;
    --card-white: #ffffff;
    --accent-red: #d0342c;
    --text-light: #f2f2f2;
    --figure-dark: #1c1c1c;
    --figure-mid: #2e2e2e;
  }
  * { margin: 0; padding: 0; box-sizing: border-box; }
  html, body {
    width: 1200px; height: 802px; overflow: hidden;
    background: var(--backdrop);
    font-family: "Open Sans", Arial, sans-serif;
  }
  .canvas { position: relative; width: 1200px; height: 802px; }
  .card {
    position: absolute; top: 274px;
    width: 442px; height: 264px; overflow: hidden;
  }
  .card--front { left: 136px; background: var(--card-black); }
  .card--back { left: 624px; background: var(--card-white); }

  .front__band {
    position: absolute; left: 0; top: 0; width: 64px; height: 100%;
    background: var(--accent-red);
  }
  .front__portrait {
    position: absolute; left: 0; top: 0; width: 214px; height: 100%;
    background: linear-gradient(160deg, var(--figure-mid), var(--figure-dark) 70%);
    border-radius: 70px 60px 0 0;
  }
  .front__info {
    position: absolute; left: 218px; top: 62px;
    color: var(--text-light);
  }
  .front__name {
    color: var(--accent-red); font-weight: 700;
    font-size: 16.5px; line-height: 20px;
  }
  .front__role { font-size: 12.5px; line-height: 16px; }
  .contact-list { list-style: none; margin-top: 11px; }
  .contact-list li {
    display: flex; align-items: center; gap: 4px;
    font-size: 12.5px; line-height: 16px;
  }
  .contact-list svg { width: 11px; height: 11px; flex: none; }
  .front__company {
    margin-top: 12px; color: var(--accent-red);
    font-weight: 700; font-size: 12.5px; line-height: 16px;
  }
  .front__address { font-size: 12.5px; line-height: 16px; }

  .back__brand {
    position: absolute; left: 0; right: 0; top: 184px;
    display: flex; align-items: center; justify-content: center; gap: 8px;
  }
  .back__mark { width: 10px; height: 10px; background: var(--accent-red); }
  .back__name {
    font-weight: 300; font-size: 28px; line-height: 34px; letter-spacing: 1px;
    color: var(--card-black);
  }
</style>
</head>
<body>
<main class="canvas">
  <section class="card card--front" aria-label="Card front">
    <div class="front__band"></div>
    <div class="front__portrait" role="img" aria-label="Illustrated portrait of the magician in a dark jacket holding a playing card"></div>
    <div class="front__info">
      <p class="front__name">MARC RAVOULET</p>
      <p class="front__role">Magician</p>
      <ul class="contact-list">
        <li>
          <svg viewBox="0 0 12 12"><path fill="#d0342c" d="M1 4c0-2 2-3 5-3s5 1 5 3l-2 1-1-1.5H4L3 5zM3 6h6l1 5H2z"/></svg>
          0492 946 157
        </li>
        <li>
          <svg viewBox="0 0 12 12"><path fill="#d0342c" d="M1 4c0-2 2-3 5-3s5 1 5 3l-2 1-1-1.5H4L3 5zM3 6h6l1 5H2z"/></svg>
          0674 219 503
        </li>
        <li>
          <svg viewBox="0 0 12 12"><rect x="1" y="2.5" width="10" height="7" fill="#d0342c"/><path d="M1.5 3l4.5 3.5L10.5 3" stroke="#000" stroke-width="1" fill="none"/></svg>
          contact@verlindoillusions.example
        </li>
        <li>
          <svg viewBox="0 0 12 12"><circle cx="6" cy="6" r="5" fill="#d0342c"/><path d="M3 4.5q2 1 2 3M7 3q1 2 2 2" stroke="#000" stroke-width="1" fill="none"/></svg>
          www.verlindoillusions.example
        </li>
      </ul>
      <p class="front__company">MAGICIAN VERLINDO</p>
      <p class="front__address">17 rue des Tilleuls - 48210</p>
      <p class="front__address">VALORCY</p>
    </div>
  </section>

  <section class="card card--back" aria-label="Card back">
    <div class="back__brand">
      <span class="back__mark"></span>
      <span class="back__name">VERLINDO</span>
    </div>
  </section>
</main>
</body>
</html>
```